Website Design for recruiting company

We need a homepage mockup for a recruiting company focused on the legal industry. Use your creative talent to come up with something visually appeal and professional for this web-site.

We'd really like to see the maze from the logo incorporated into the design somehow. Please use the website mockup provided as inspiration for this project. We really like the layout and photos!

Target Market(s)

lawyers

Industry/Entity Type

Legal

Number of Pages Required

1 page

Font styles to use
Sans Serif

```html
<!DOCTYPE html>
<html lang="en">
<head>
<meta charset="utf-8">
<title>Harbor Legal Search — Home</title>
<link href="https://fonts.googleapis.com/css2?family=Lato:wght@400;700;900&display=swap" rel="stylesheet">
<style>
:root{
  --orange:#f7931e;
  --ink:#4a4a4a;
  --heading:#58595b;
  --muted:#8a8a8a;
  --panel:#f3f3f3;
  --footer:#625463;
  --footer-text:#e9e4ea;
  --white:#ffffff;
}
*{box-sizing:border-box;margin:0;padding:0}
html,body{width:1200px;height:4051px;overflow:hidden}
body{font-family:'Lato',sans-serif;color:var(--ink);background:var(--white);position:relative}
.abs{position:absolute}

/* hero */
.hero{left:0;top:0;width:1200px;height:678px;
  background:linear-gradient(100deg,#2e3540 0%,#6b7380 30%,#a7a7a5 55%,#8c7565 78%,#5a4b44 100%)}
.hero::after{content:"";position:absolute;inset:0;background:rgba(20,24,32,.28)}
.brand{left:75px;top:26px;display:flex;align-items:center;gap:14px;z-index:2}
.brand-dot{width:100px;height:100px;border-radius:50%;border:3px solid rgba(255,255,255,.85)}
.brand-name{color:#e8e8e8;font-size:16px;font-weight:400}
.nav{left:535px;top:66px;z-index:2}
.nav a{position:absolute;color:var(--white);font-size:14px;font-weight:700;text-decoration:none;white-space:nowrap;top:0}
.nav a.active::after{content:"";position:absolute;left:-12px;right:-12px;top:24px;height:3px;background:var(--orange)}
.hero-title{left:0;width:1200px;top:302px;text-align:center;color:var(--white);z-index:2}
.hero-title h1{font-size:74px;font-weight:900;line-height:1;letter-spacing:1px}
.hero-title p{font-size:34px;font-weight:900;margin-top:8px}

/* about */
.about-frame{left:0;top:678px;width:571px;height:453px;background:var(--orange)}
.about-photo{left:16px;top:694px;width:571px;height:424px;background:linear-gradient(135deg,#5d6165,#b8b6b2 50%,#3e4247)}
.about-text{left:613px;top:748px;width:515px}
h2.section{font-size:34px;font-weight:900;color:var(--heading);letter-spacing:.3px}
.about-text p{font-size:16.5px;line-height:31.5px;margin-top:26px;color:var(--ink)}
.link-more{display:inline-block;margin-top:22px;font-size:16px;font-weight:900;color:var(--heading);text-decoration:none}
.arrow{display:inline-block;width:12px;height:12px;vertical-align:middle;margin-left:8px}

/* what's new */
.news{left:0;top:1203px;width:1200px;height:1746px;background:var(--panel)}
.news-head{left:75px;top:1257px}
.btn{display:inline-flex;align-items:center;justify-content:center;font-weight:900;font-size:16px;text-decoration:none}
.btn-orange{background:var(--orange);color:var(--white)}
.btn-outline{border:3px solid var(--heading);color:var(--heading);background:transparent}
.search-btn{left:961px;top:1258px;width:165px;height:43px}
.job{left:75px;width:1051px;height:283px;background:var(--white)}
.job-photo{position:absolute;top:35px;width:306px;height:217px}
.job-body{position:absolute;top:36px;width:666px}
.job.left .job-photo{left:24px}
.job.left .job-body{left:359px}
.job.right .job-photo{left:721px}
.job.right .job-body{left:30px;width:660px}
.job-title{font-size:16px;font-weight:900;color:var(--ink)}
.job-id{position:absolute;right:8px;top:0;font-size:15px;color:var(--muted)}
.job.right .job-id{right:0}
.job-date{font-size:14px;color:var(--muted);margin-top:14px}
.job-desc{font-size:14.2px;line-height:27.5px;margin-top:10px;color:var(--ink)}
.job .btn{height:39px;width:122px;font-size:14px;margin-top:16px}

/* employers */
.emp-text{left:75px;top:3117px;width:495px}
.emp-text p{font-size:16.5px;line-height:31.5px;margin-top:22px}
.emp-buttons{left:75px;top:3312px;display:flex;gap:11px}
.emp-buttons .btn{height:51px}
.emp-frame{left:632px;top:3020px;width:568px;height:453px;background:var(--orange)}
.emp-photo{left:613px;top:3035px;width:571px;height:422px;background:linear-gradient(120deg,#aeb6bd,#4e5357 45%,#2f3236 70%,#8a8f94)}

/* footer */
.footer{left:0;top:3547px;width:1200px;height:504px;background:var(--footer)}
.f-brand{left:75px;top:3589px;display:flex;align-items:center;gap:10px}
.f-brand .brand-dot{width:72px;height:72px;border:2px solid #ddd}
.f-brand span{font-size:11px;color:var(--footer-text)}
.social{display:flex;gap:22px;align-items:center}
.social span{width:20px;height:20px;border-radius:4px;background:var(--white);display:block}
.social-top{left:740px;top:3614px}
.contact-btn{left:945px;top:3603px;width:181px;height:41px;border:3px solid var(--white);color:var(--white);font-size:16px}
.f-col{top:3713px;width:260px;color:var(--footer-text)}
.f-col h3{font-size:18px;font-weight:900;color:var(--white)}
.f-col ul{list-style:none;margin-top:12px}
.f-col li{font-size:14px;line-height:36px}
.f-contact li{display:flex;align-items:flex-start;gap:18px;line-height:26px;margin-bottom:6px}
.f-contact svg{flex:none;margin-top:6px}
.f-rule{left:75px;top:3971px;width:1051px;height:1px;background:rgba(255,255,255,.25)}
.copyright{left:75px;top:4006px;font-size:12.5px;color:var(--footer-text)}
.social-bottom{left:975px;top:4004px}
</style>
</head>
<body>

<!-- Hero -->
<section class="abs hero" role="img" aria-label="Photo of smiling legal professionals in a meeting"></section>
<div class="abs brand">
  <span class="brand-dot"></span>
  <span class="brand-name">harbor legal search</span>
</div>
<nav class="abs nav">
  <a class="active" style="left:0">HOME</a>
  <a style="left:85px">ABOUT US</a>
  <a style="left:199px">WHAT’S NEW</a>
  <a style="left:335px">FOR EMPLOYERS</a>
  <a style="left:497px">CONTACT US</a>
</nav>
<div class="abs hero-title">
  <h1>START HERE</h1>
  <p>LET OUR EXPERIENCE GUIDE YOU</p>
</div>

<!-- About -->
<div class="abs about-frame"></div>
<div class="abs about-photo" role="img" aria-label="Photo of a confident attorney standing in front of her team"></div>
<div class="abs about-text">
  <h2 class="section">ABOUT US</h2>
  <p>Harbor Legal Search focuses on the permanent placement of attorneys with law firms and corporations in the New England area. Founded in 1982, Harbor Legal Search is the oldest attorney search firm in New England, and is ranked the number one legal recruiter in New England in the most recent survey conducted by The Counsel Review .</p>
  <a class="link-more" href="#">LEARN MORE<svg class="arrow" viewBox="0 0 12 12"><path d="M1 6h9M6 2l4 4-4 4" stroke="#58595b" stroke-width="2.4" fill="none"/></svg></a>
</div>

<!-- What's new -->
<section class="abs news"></section>
<h2 class="abs section news-head">WHAT’S NEW</h2>
<a class="abs btn btn-orange search-btn" href="#">SEARCH JOBS</a>

<article class="abs job left" style="top:1334px">
  <div class="job-photo" role="img" aria-label="Photo of colleagues in a medical technology lab" style="background:linear-gradient(135deg,#d9dde0,#8d9aa3 55%,#4d5a60)"></div>
  <div class="job-body">
    <div class="job-title">IN-HOUSE/CORPORATE/M&amp;A</div><span class="job-id">Job Id: 2772</span>
    <div class="job-date">Listing Date: 02/10/2020</div>
    <p class="job-desc">Global publicly listed medical technology leader seeks 8+ year M&amp;A specialist with major law firm training for lead role on all M&amp;A and other BD transactions. As a key member of the leadership team, this role will partner with the Vice President, Corporate Business &nbsp;Development to lead M&amp;A transactions from inception to closing and working effectively with Business Development.</p>
    <a class="btn btn-outline" href="#">MORE INFO</a>
  </div>
</article>

<article class="abs job right" style="top:1644px">
  <div class="job-body">
    <div class="job-title">ASSOCIATE/LITIGATION</div><span class="job-id">Job Id: 2778</span>
    <div class="job-date">Listing Date: 02/04/2020</div>
    <p class="job-desc">Highly regarded mid-size national firm seeks litigation associate with 4-8 years of experience to join their Litigation Practice. This associate will work on a wide array of litigation matters including, construction, real estate, employment, shareholder and general business disputes. Fantastic opportunity to deal directly with clients and gain hands-on experience.</p>
    <a class="btn btn-outline" href="#">MORE INFO</a>
  </div>
  <div class="job-photo" role="img" aria-label="Photo of a contract being signed beside a gavel" style="background:linear-gradient(135deg,#3a3633,#9a928a 50%,#d8d4cf)"></div>
</article>

<article class="abs job left" style="top:1955px">
  <div class="job-photo" role="img" aria-label="Photo of a biotech researcher working in a lab" style="background:linear-gradient(135deg,#2f6fb0,#7fb6e3 50%,#c9e3f4)"></div>
  <div class="job-body">
    <div class="job-title">IN-HOUSE/BIOTECH/CONTRACTS</div><span class="job-id">Job Id: 2777</span>
    <div class="job-date">Listing Date: 01/28/2020</div>
    <p class="job-desc">Outstanding opportunity for 3+ year attorney to join a premier biotech company in contracts counsel role. Prior experience drafting and negotiating biotech agreements including Clinical Trial Agreements, Master Service Agreements and related research and development contracts<br>is required.</p>
    <a class="btn btn-outline" href="#">MORE INFO</a>
  </div>
</article>

<article class="abs job right" style="top:2265px">
  <div class="job-body">
    <div class="job-title">IN-HOUSE/INVESTMENT MANAGEMENT</div><span class="job-id">Job Id: 2770</span>
    <div class="job-date">Listing Date: 01/03/2020</div>
    <p class="job-desc">Large Boston-based investment manager seeks 3rd – 5th year investment management attorney with major law firm training to provide direct, day-to-day support to the firm’s clients and key business groups such as trading/portfolio management, investment services, client operations/relationship management and business development.</p>
    <a class="btn btn-outline" href="#">MORE INFO</a>
  </div>
  <div class="job-photo" role="img" aria-label="Photo of advisors reviewing charts on a tablet and laptop" style="background:linear-gradient(135deg,#4a4038,#c8a98a 50%,#e9ddd0)"></div>
</article>

<article class="abs job left" style="top:2576px">
  <div class="job-photo" role="img" aria-label="Photo of a scientist at a microscope beside a monitor" style="background:linear-gradient(135deg,#e4e7ea,#a8b6c2 50%,#4d6b86)"></div>
  <div class="job-body">
    <div class="job-title">IN-HOUSE /LIFE SCIENCES / SECURITIES</div><span class="job-id">Job Id: 2773</span>
    <div class="job-date">Listing Date: 01/14/2020</div>
    <p class="job-desc">Terrific opportunity for 3rd – 6th year corporate attorney to join outstanding MA-based publicly listed biopharmaceutical company. Major firm and strong securities and corporate governance experience required, including demonstrated knowledge of U.S. securities law and experience coordinating filings and disclosures.</p>
    <a class="btn btn-outline" href="#">MORE INFO</a>
  </div>
</article>

<!-- For employers -->
<div class="abs emp-text">
  <h2 class="section">FOR EMPLOYERS</h2>
  <p>Our unparalleled recruiting industry and legal experience have generated an extensive network of contacts throughout the legal community.</p>
</div>
<div class="abs emp-buttons">
  <a class="btn btn-orange" href="#" style="width:310px">FIND THE RIGHT CANDIDATE<svg class="arrow" viewBox="0 0 12 12"><path d="M1 6h9M6 2l4 4-4 4" stroke="#fff" stroke-width="2.4" fill="none"/></svg></a>
  <a class="btn btn-outline" href="#" style="width:155px">START HERE<svg class="arrow" viewBox="0 0 12 12"><path d="M1 6h9M6 2l4 4-4 4" stroke="#58595b" stroke-width="2.4" fill="none"/></svg></a>
</div>
<div class="abs emp-frame"></div>
<div class="abs emp-photo" role="img" aria-label="Photo of two colleagues laughing in a bright office"></div>

<!-- Footer -->
<footer class="abs footer"></footer>
<div class="abs f-brand"><span class="brand-dot"></span><span>harbor legal search</span></div>
<div class="abs social social-top" aria-label="Social links"><span></span><span></span><span></span><span></span></div>
<a class="abs btn contact-btn" href="#">CONTACT US<svg class="arrow" viewBox="0 0 12 12"><path d="M1 6h9M6 2l4 4-4 4" stroke="#fff" stroke-width="2.4" fill="none"/></svg></a>

<div class="abs f-col" style="left:75px"><h3>ABOUT US</h3><ul><li>Morbi lacinia leo</li><li>Libero et convallis</li><li>Metus hendrerit</li><li>Interdum et malesuada</li><li>Fames ac ante</li></ul></div>
<div class="abs f-col" style="left:343px"><h3>WHAT’S NEWS</h3><ul><li>Morbi lacinia leo</li><li>Libero et convallis</li><li>Metus hendrerit</li><li>Interdum et malesuada</li><li>Fames ac ante</li></ul></div>
<div class="abs f-col" style="left:613px"><h3>RESOURCES</h3><ul><li>Morbi lacinia leo</li><li>Libero et convallis</li><li>Metus hendrerit</li><li>Interdum et malesuada</li><li>Fames ac ante</li></ul></div>
<div class="abs f-col f-contact" style="left:884px;width:250px"><h3>CONTACT INFO</h3>
  <ul>
    <li style="display:block">P.O. Box 4400, Harbor City<br>ST 00100</li>
    <li><svg width="14" height="14" viewBox="0 0 14 14"><path d="M3 1l3 3-2 2c1 2 2 3 4 4l2-2 3 3-2 2C6 13 1 8 1 3z" fill="#e9e4ea"/></svg>555.210.4400</li>
    <li><svg width="14" height="14" viewBox="0 0 14 14"><rect x="1" y="5" width="12" height="8" fill="#e9e4ea"/><rect x="3" y="1" width="8" height="5" fill="none" stroke="#e9e4ea" stroke-width="1.5"/></svg>555.210.4410</li>
    <li><svg width="14" height="14" viewBox="0 0 14 14"><rect x="1" y="3" width="12" height="9" fill="#e9e4ea"/><path d="M1 3l6 5 6-5" stroke="#625463" stroke-width="1.3" fill="none"/></svg>info@harborlegalsearch.com</li>
  </ul>
</div>
<div class="abs f-rule"></div>
<div class="abs copyright">Copyright &nbsp;© 2020 Company Name. &nbsp;All Rights Reserved</div>
<div class="abs social social-bottom" aria-label="Social links"><span></span><span></span><span></span><span></span></div>

</body>
</html>
```